Business Card Design for my Real Estate Investing Company

This is for a Real Estate Investing Company that will be serving the Las Vegas Valley. Id like the following slogan included: "Investing in Our Community" I have attached my logo. You will see the color tones I'm interested in..in my logo. I would like the card to be double-sided with a modern, professional look.
Target Market(s)
Homeowners, banks, real estate industry
Industry/Entity Type
Real Estate
Contact Information for Business Card
name: Dale Harwick
position: Managing Member
address: 4821 Corliss Pkwy ste 207-300
N. Las Vegas, NV 89084
phone: (702) 555-0143
fax: (702) 555-0187
email: SummitRidgeEstate@hollowmail.test
web: SummitRidgeEstates.test
*At the bottom of the card I would like....
We buy houses for cash....no repairs, no commissions, no fees!
Logo Text
SUMMIT RIDGE ESTATES "Investing in Our Community"
Font styles to use
Other font styles liked:
- Lora
Requirements
Must have
- On the back of the card, i'd like to have my logo large and the following statements:
- Are you considering selling your home? Want a simple, hassle-free transaction? We can help! We buy houses for cash and can close quickly! No need to do any repairs, no realtor commissions, no closing costs.....and no headaches. Let us help you with your real estate needs...!
Nice to have
- multiple colors 2 two tone on front and back

```html
<!DOCTYPE html>
<html lang="en">
<head>
<meta charset="utf-8">
<title>Summit Ridge Estates — Business Card</title>
<link rel="stylesheet" href="https://fonts.googleapis.com/css2?family=Lora:ital,wght@0,400;0,700;1,700&family=Open+Sans:wght@400;600&display=swap">
<style>
  :root {
    --bg: #ebebeb;
    --card-white: #fafafa;
    --brand-blue: #1160ad;
    --accent-orange: #e07a2a;
    --ink: #3a3a3a;
    --muted: #6b6b6b;
    --on-blue: #ffffff;
  }
  * { box-sizing: border-box; margin: 0; padding: 0; }
  html, body {
    width: 1200px; height: 900px; overflow: hidden;
    background: var(--bg);
  }
  .canvas {
    width: 1200px; height: 900px;
    display: flex; align-items: center; justify-content: center; gap: 40px;
  }
  .card {
    width: 520px; height: 297px;
    position: relative;
    box-shadow: 0 2px 6px rgba(0,0,0,.12);
  }

  /* Wordmark: invented name in one colour and weight, one plain square */
  .wordmark {
    font-family: "Lora", serif; font-weight: 700;
    display: flex; align-items: center; justify-content: center; gap: 10px;
    white-space: nowrap;
  }
  .wordmark__square { width: 12px; height: 12px; background: currentColor; flex: none; }

  /* Front */
  .card--front { background: var(--card-white); color: var(--ink); padding: 30px 36px; }
  .card--front .wordmark { color: var(--brand-blue); font-size: 26px; justify-content: flex-end; }
  .contact { margin-top: 26px; font-family: "Open Sans", sans-serif; font-size: 11.5px; line-height: 1.55; }
  .contact__name { font-family: "Lora", serif; font-weight: 700; color: var(--brand-blue); font-size: 14px; }
  .contact__role { color: var(--muted); font-size: 11px; margin-bottom: 4px; }
  .contact__label { color: var(--brand-blue); font-weight: 600; }
  .tagline {
    margin-top: 12px;
    font-family: "Lora", serif; font-style: italic; font-weight: 700;
    color: var(--brand-blue); font-size: 13px;
  }

  /* Back */
  .card--back {
    background: var(--brand-blue); color: var(--on-blue);
    padding: 42px 30px; text-align: center;
    border-bottom: 3px solid var(--accent-orange);
  }
  .card--back .wordmark { font-size: 30px; }
  .pitch {
    margin-top: 22px;
    font-family: "Open Sans", sans-serif; font-size: 12.5px; line-height: 1.45;
  }
  .pitch__slogan { margin-top: 8px; font-weight: 600; }
</style>
</head>
<body>
<main class="canvas">
  <section class="card card--front" aria-label="Business card front">
    <div class="wordmark"><span class="wordmark__square"></span>Summit Ridge Estates</div>
    <div class="contact">
      <div class="contact__name">Dale Harwick</div>
      <div class="contact__role">Managing Member</div>
      <div><span class="contact__label">P:</span> (702) 555-0143 | <span class="contact__label">F:</span> (702) 555-0187</div>
      <div><span class="contact__label">E:</span> SummitRidgeEstate@hollowmail.test | <span class="contact__label">W:</span> SummitRidgeEstates.test</div>
      <div>4821 Corliss Pkwy ste 207-300 N. Las Vegas, NV 89084</div>
    </div>
    <p class="tagline">We buy houses for cash.... no repairs, no commissions, no fees!</p>
  </section>

  <section class="card card--back" aria-label="Business card back">
    <div class="wordmark"><span class="wordmark__square"></span>Summit Ridge Estates</div>
    <p class="pitch">
      Are you considering selling your home?<br>
      Want a simple, hassle-free transaction?<br>
      We can help! We buy houses for cash and can close quickly!<br>
      No need to do any repairs, no realtor commissions,<br>
      no closing costs.....and no headaches.<br>
      Let us help you with your real estate needs...!
    </p>
    <p class="pitch pitch__slogan">Investing in Our Community</p>
  </section>
</main>
</body>
</html>
```